Black Car Limousine transportation business in Naples Florida

Always stand for my reliability and RVD stands for Love, K and M are the first initials of my children's names. It should show professionalism and a dedication to customer service. We keep our clients identities private. Show our professionalism. We are Black car Black tie company. We service transportation on a reserve basis to and from residents, airports, casinos, hotels,

Target Market(s)

It is a Private car service. High end clients. Businesses, Celebrity and athletes. Service to airports, hotels, special events.

Industry/Entity Type

Business

Contact Information for Business Card

A pearl metallic or Luster card. Standard business card size. Would like the name, Company email, show we take credit cards and phone number. Currently I don't have a website but will like to add later.

Logo Text

STEADFAST RVD TRANSPORTATION

Font styles to use
Serif

Colors
eaeaea
000000

Requirements
Must have
• Must have Company email, show we take credit cards and phone number. Currently I don't have a website but will like to add later.
Nice to have
• Would like to stay with a black and white theme. Open to some color trim.
Should not have
• Open to suggestions

```html
<!DOCTYPE html>
<html lang="en">
<head>
<meta charset="utf-8">
<title>Steadfast RVD Transportation – Business Card</title>
<link rel="stylesheet" href="https://fonts.googleapis.com/css2?family=Open+Sans:ital,wght@0,400;0,600;0,700;1,700&display=swap">
<style>
  :root {
    --stage: #b9b9b9;
    --card: #ffffff;
    --ink: #000000;
    --ink-soft: #4a4a4a;
    --logo-grey: #8c8c8c;
    --vehicle-dark: #1a1a1a;
    --vehicle-mid: #5a5a5a;
  }
  * { box-sizing: border-box; margin: 0; padding: 0; }
  html, body { width: 1105px; height: 1200px; overflow: hidden; }
  body {
    background: var(--stage);
    font-family: "Open Sans", Arial, sans-serif;
    color: var(--ink);
    position: relative;
  }
  .card {
    position: absolute;
    left: 193px;
    width: 720px;
    height: 411px;
    background: var(--card);
    box-shadow: 3px 4px 7px rgba(0,0,0,0.45);
  }
  .card--front { top: 167px; }
  .card--back { top: 623px; }

  .brand {
    position: absolute;
    left: 400px;
    top: 62px;
    width: 285px;
    display: flex;
    align-items: center;
    gap: 10px;
  }
  .brand__mark {
    width: 14px; height: 14px;
    background: var(--logo-grey);
    flex: none;
  }
  .brand__name {
    font-weight: 700;
    font-size: 17px;
    line-height: 1.15;
    letter-spacing: 1px;
    color: var(--logo-grey);
  }

  .accent-bar {
    position: absolute;
    left: 0; top: 217px;
    width: 18px; height: 145px;
    background: var(--ink);
  }
  .person {
    position: absolute;
    left: 58px; top: 212px;
  }
  .person__name {
    font-weight: 600;
    font-size: 27px;
    line-height: 1.1;
  }
  .person__role {
    font-size: 19px;
    color: var(--ink-soft);
    margin-top: 2px;
  }
  .contact {
    position: absolute;
    left: 58px; top: 282px;
    list-style: none;
  }
  .contact__item {
    display: flex;
    align-items: center;
    height: 27.5px;
    font-size: 18px;
    color: var(--ink-soft);
  }
  .contact__icon {
    width: 18px; height: 18px;
    margin-right: 10px;
    fill: var(--ink);
  }

  .vehicle {
    position: absolute;
    left: 152px; top: 130px;
    width: 387px; height: 156px;
    border-radius: 40px 60px 18px 18px;
    background: linear-gradient(180deg, var(--vehicle-mid) 0%, var(--vehicle-dark) 60%, var(--ink) 100%);
  }
  .payment {
    position: absolute;
    left: 0; right: 0; top: 334px;
    display: flex;
    justify-content: center;
    align-items: center;
    gap: 6px;
    font-weight: 700;
    font-style: italic;
    font-size: 19px;
  }
  .payment__icon { width: 30px; height: 22px; }
</style>
</head>
<body>
  <section class="card card--front">
    <div class="brand">
      <span class="brand__mark"></span>
      <span class="brand__name">STEADFAST RVD TRANSPORTATION</span>
    </div>

    <div class="accent-bar"></div>
    <div class="person">
      <h1 class="person__name">DANIEL REYES</h1>
      <p class="person__role">CEO/Founder</p>
    </div>
    <ul class="contact">
      <li class="contact__item">
        <svg class="contact__icon" viewBox="0 0 24 24"><path d="M6.6 10.8c1.4 2.8 3.8 5.1 6.6 6.6l2.2-2.2c.3-.3.7-.4 1-.2 1.1.4 2.3.6 3.6.6.6 0 1 .4 1 1V20c0 .6-.4 1-1 1C10.6 21 3 13.4 3 4c0-.6.4-1 1-1h3.5c.6 0 1 .4 1 1 0 1.3.2 2.5.6 3.6.1.3 0 .7-.2 1z"/></svg>
        555 014 2290
      </li>
      <li class="contact__item">
        <svg class="contact__icon" viewBox="0 0 24 24"><path d="M2 5h20v14H2z M2 5l10 7 10-7" /><path d="M3 6l9 6.3L21 6v12H3z" fill="#fff" opacity="0"/></svg>
        hello@steadfastrvd.com
      </li>
      <li class="contact__item">
        <svg class="contact__icon" viewBox="0 0 24 24"><circle cx="12" cy="12" r="10"/><path d="M7 7c2 1 3 3 2 5s1 3 2 4M15 5c-1 2 0 3 2 3s3 2 2 4" stroke="#fff" stroke-width="1.6" fill="none"/></svg>
        www.steadfastrvd.com
      </li>
    </ul>
  </section>

  <section class="card card--back">
    <div class="vehicle" role="img" aria-label="Photo of a black luxury SUV, side-front view"></div>
    <p class="payment">
      <svg class="payment__icon" viewBox="0 0 30 22"><rect x="2" y="3" width="26" height="16" rx="2.5" fill="var(--ink)"/><rect x="2" y="7" width="26" height="3" fill="#fff"/><rect x="6" y="13" width="8" height="2" fill="#fff"/></svg>
      We accept credit cards
    </p>
  </section>
</body>
</html>
```